Professionally crafted, customizable corporate CV template

A versatile CV template in both Microsoft Word and Adobe PDF formats, ensuring accessibility and ease of use for all users.
A comprehensive user guide that provides clear instructions on how to personalize the CV template, including adding or omitting sections based on individual needs.
The template will feature a sleek, professional layout incorporating your company's color scheme, logo, and fonts, making each CV a reflection of your corporate identity.
The template will have a placeholder for a photo of the candidate
The template should have 2 pages
Company Website: https://pebble-orchard.io
CV Language: English

```html
<!DOCTYPE html>
<html lang="en">
<head>
<meta charset="utf-8">
<title>Lorem Ipsum – Curriculum Vitae</title>
<link rel="stylesheet" href="https://fonts.googleapis.com/css2?family=Montserrat:wght@400;500;600;700;800&display=swap">
<style>
  :root {
    --backdrop: #dfe1e5;
    --paper: #ffffff;
    --brand-blue: #0f4f8a;
    --brand-blue-dark: #0b3f70;
    --slate: #676b79;
    --slate-dark: #585c69;
    --mist: #ececf1;
    --ink: #1d2433;
    --on-blue: #ffffff;
  }
  * { box-sizing: border-box; margin: 0; padding: 0; }
  html, body {
    width: 1200px; height: 800px; overflow: hidden;
    background: var(--backdrop);
    font-family: "Montserrat", sans-serif;
    color: var(--ink);
  }
  .resume {
    position: absolute; left: 317px; top: 4px;
    width: 566px; height: 792px;
    background: var(--paper);
    overflow: hidden;
    box-shadow: 0 2px 10px rgba(0,0,0,.12);
  }
  .resume__sidebar-bg {
    position: absolute; left: 0; top: 0; bottom: 0; width: 222px;
    background: var(--brand-blue);
  }
  .resume__header-shapes { position: absolute; left: 0; top: 0; width: 566px; height: 200px; }
  .resume__name {
    position: absolute; left: 22px; top: 72px;
    color: var(--on-blue); font-weight: 800; font-size: 35px; letter-spacing: 1px;
  }
  .resume__photo {
    position: absolute; left: 398px; top: 30px; width: 144px; height: 144px;
    border-radius: 50%;
    border: 5px solid var(--slate);
    background: linear-gradient(160deg, #eef0f4 0%, #c9cfdb 55%, #3a5694 100%);
  }

  /* Sidebar */
  .sidebar {
    position: absolute; left: 0; top: 140px; width: 222px;
    padding: 0 18px 0 22px; color: var(--on-blue);
  }
  .contact { list-style: none; font-size: 9.5px; line-height: 1.3; }
  .contact li { display: flex; align-items: flex-start; gap: 7px; margin-bottom: 5px; }
  .contact__icon {
    flex: none; width: 13px; height: 13px; border-radius: 50%;
    background: var(--on-blue); display: flex; align-items: center; justify-content: center;
  }
  .contact__icon svg { width: 8px; height: 8px; }
  .contact__phone { font-weight: 700; font-size: 11px; }

  .pill {
    display: inline-block; padding: 3px 12px; border-radius: 12px;
    font-weight: 800; font-size: 10.5px; letter-spacing: .4px; text-transform: uppercase;
  }
  .pill--light { background: var(--on-blue); color: var(--brand-blue); }
  .pill--blue { background: var(--brand-blue); color: var(--on-blue); }

  .side-section { margin-top: 22px; }
  .side-section .pill { margin-bottom: 7px; }

  .bullets { list-style: none; font-size: 8.4px; line-height: 1.35; }
  .bullets li { position: relative; padding-left: 11px; margin-bottom: 1.5px; }
  .bullets li::before {
    content: ""; position: absolute; left: 0; top: 3px;
    width: 5px; height: 5px; border-radius: 50%;
    border: 1.3px solid currentColor;
  }

  /* Main column */
  .main { position: absolute; left: 240px; top: 186px; width: 306px; }
  .brand {
    display: flex; align-items: center; gap: 6px;
    color: var(--brand-blue); font-weight: 700; font-size: 12px; letter-spacing: .3px;
    margin-bottom: 10px;
  }
  .brand__dot { width: 12px; height: 12px; border-radius: 50%; background: var(--brand-blue); }
  .summary-text { font-size: 8.4px; line-height: 1.4; margin: 6px 0 14px; }
  .expertise { margin-top: 4px; }
  .role { margin-top: 9px; }
  .role__title { color: var(--brand-blue); font-weight: 700; font-size: 9.5px; margin-bottom: 3px; }
  .role .bullets { color: var(--ink); }
  .role .bullets li::before { border-color: var(--brand-blue); }
</style>
</head>
<body>
<article class="resume">
  <div class="resume__sidebar-bg"></div>
  <svg class="resume__header-shapes" viewBox="0 0 566 200" aria-hidden="true">
    <rect x="222" y="0" width="344" height="62" fill="var(--mist)"/>
    <polygon points="430,20 566,20 566,52 410,52" fill="var(--slate-dark)"/>
    <polygon points="0,58 400,58 370,128 0,128" fill="var(--slate)"/>
  </svg>
  <h1 class="resume__name">LOREM IPSUM</h1>
  <div class="resume__photo" role="img" aria-label="Candidate portrait photo placeholder"></div>

  <aside class="sidebar">
    <ul class="contact">
      <li><span class="contact__icon"><svg viewBox="0 0 10 10"><path d="M5 1a3 3 0 0 0-3 3c0 2.2 3 5 3 5s3-2.8 3-5a3 3 0 0 0-3-3z" fill="var(--brand-blue)"/></svg></span>48 Orchard Lane,<br>Harbor District</li>
      <li><span class="contact__icon"><svg viewBox="0 0 10 10"><path d="M2 1h2l1 2-1 1a5 5 0 0 0 2 2l1-1 2 1v2c0 .6-.4 1-1 1A7 7 0 0 1 1 2c0-.6.4-1 1-1z" fill="var(--brand-blue)"/></svg></span><span class="contact__phone">(555)014-2278</span></li>
      <li><span class="contact__icon"><svg viewBox="0 0 10 10"><rect x="1" y="2.5" width="8" height="5" fill="var(--brand-blue)"/><path d="M1 2.5l4 3 4-3" stroke="#fff" stroke-width=".8" fill="none"/></svg></span>hello@pebble-orchard.io</li>
      <li><span class="contact__icon"><svg viewBox="0 0 10 10"><circle cx="5" cy="5" r="4" fill="none" stroke="var(--brand-blue)" stroke-width="1"/><path d="M1 5h8M5 1c-2 2.5-2 5.5 0 8M5 1c2 2.5 2 5.5 0 8" stroke="var(--brand-blue)" stroke-width=".8" fill="none"/></svg></span>www.pebble-orchard.io</li>
    </ul>

    <section class="side-section">
      <h2 class="pill pill--light">Qualifications</h2>
      <ul class="bullets">
        <li>Master Mariner Unlimited</li>
        <li>Nautical Science Degree</li>
        <li>Offshore Installation Manager Unlimited</li>
        <li>Dynamic Positioning Operator Unlimited</li>
        <li>Maritime Guild Accredited Instructor</li>
        <li>Harbor College Teaching Diploma</li>
        <li>Management of Major Emergencies Certification</li>
      </ul>
    </section>

    <section class="side-section">
      <h2 class="pill pill--light">Education</h2>
      <ul class="bullets">
        <li>Master Mariner Unlimited</li>
        <li>Nautical Science Degree</li>
        <li>Offshore Installation Manager Unlimited</li>
        <li>Dynamic Positioning Operator Unlimited</li>
        <li>Maritime Guild Accredited Instructor</li>
        <li>Harbor College Teaching Diploma</li>
        <li>Management of Major Emergencies Certification</li>
      </ul>
    </section>

    <section class="side-section">
      <h2 class="pill pill--light">Key Skills</h2>
      <ul class="bullets">
        <li>Project Management</li>
        <li>Business Development</li>
        <li>Marketing and Contract Negotiations</li>
        <li>Team Management</li>
        <li>New Build and Retrofit Projects</li>
        <li>Policy and Procedure Development</li>
        <li>First Nations Engagement</li>
        <li>Problem Solving</li>
        <li>Emergency Management and Response</li>
        <li>Culture Improvement</li>
      </ul>
    </section>
  </aside>

  <main class="main">
    <div class="brand"><span class="brand__dot"></span>PEBBLE ORCHARD</div>

    <section>
      <h2 class="pill pill--blue">Summary</h2>
      <p class="summary-text">Understanding the complexity and challenges of on prem deployments based on years of experience help us design sustainable and reliable cloud infrastructure. Hands on experience and skills in a big range of tools, systems &amp; applications help us getting the best out of the cloud.</p>
    </section>

    <section class="expertise">
      <h2 class="pill pill--blue">Professional Expertise</h2>

      <div class="role">
        <h3 class="role__title">Leadership and Management</h3>
        <ul class="bullets">
          <li>Professional enterprise software engineering with predictable results</li>
          <li>Minimization of production and implementation risks thanks to meticulous planning</li>
          <li>Substantial cost savings with streamlined processes and lean production practices</li>
          <li>Ease &amp; low cost of maintenance with fully documented deliverables and deployment guides</li>
        </ul>
      </div>

      <div class="role">
        <h3 class="role__title">Leadership and Management</h3>
        <ul class="bullets">
          <li>Professional enterprise software engineering with predictable results</li>
          <li>Minimization of production and implementation risks thanks to meticulous planning</li>
          <li>Substantial cost savings with streamlined processes and lean production practices</li>
          <li>Ease &amp; low cost of maintenance with fully documented deliverables and deployment guides</li>
        </ul>
      </div>

      <div class="role">
        <h3 class="role__title">Leadership and Management</h3>
        <ul class="bullets">
          <li>Professional enterprise software engineering with predictable results</li>
          <li>Minimization of production and implementation risks thanks to meticulous planning</li>
          <li>Substantial cost savings with streamlined processes and lean production practices</li>
          <li>Ease &amp; low cost of maintenance with fully documented deliverables and deployment guides</li>
        </ul>
      </div>

      <div class="role">
        <h3 class="role__title">Leadership and Management</h3>
        <ul class="bullets">
          <li>Professional enterprise software engineering with predictable results</li>
          <li>Minimization of production and implementation risks thanks to meticulous planning</li>
          <li>Substantial cost savings with streamlined processes and lean production practices</li>
          <li>Ease &amp; low cost of maintenance with fully documented deliverables and deployment guides</li>
        </ul>
      </div>
    </section>
  </main>
</article>
</body>
</html>
```